Halvik - consultancy website

I need a new design for my webpage/presence [to be functioning with Wordpress - I have a programmer to set it up but not the design idea].
My company is Halvik - a consultancy firm focused on growth management for Swedish SME's primarily;. We call it Leadership toolkit for firms on the rise, kind of a doctor helping small become big. Contentwise, its a simple frontpage + 3-4 subpages with content re company/myself/focus etc. The new site should communicate a fresh, trustworthy take yet simple and functional on all devices [i.e. think UI compatible for mobile/tablet]. Current building parts/form elements are
a) existing logo and text elements
b) existing pictures
c) the yellowish color
colours and new ideas on pictures/positioning are welcome. I prefer a 'full width page' solution with centralised text elements but that's all up to you to suggest. Current site is a quickfix made by myself - now I'm moving it to a new platform so want to take the opportunity to make it
Nothing superspecial as it is a 2-man show; on the other hand I still want to have a modern & fresh reflection of my brand in digital environments. Help me out!
www.halvik-demo.se
Best
Lina Bergqvist

```html
<!DOCTYPE html>
<html lang="en">
<head>
<meta charset="utf-8">
<title>Halvik – Consultancy</title>
<link href="https://fonts.googleapis.com/css2?family=Arimo:ital,wght@0,400;0,700;1,400&family=Gelasio:wght@400;500&display=swap" rel="stylesheet">
<style>
:root{
  --orange:#f0a23a;
  --ink:#1b1b1b;
  --text:#444;
  --muted:#8a8a8a;
  --line:#e6e6e6;
  --white:#fff;
  --footer:#1f1f1f;
  --footer-base:#111;
  --fb:#3b5998;
  --tw:#3aa9e0;
  --gp:#d9473a;
  --red:#d9342b;
}
*{margin:0;padding:0;box-sizing:border-box}
html,body{width:1200px;height:2528px;overflow:hidden}
body{position:relative;background:var(--white);font-family:"Arimo",sans-serif;color:var(--text)}
.abs{position:absolute}

/* header */
.brand{left:98px;top:26px}
.brand-name{font-family:"Gelasio",serif;font-size:50px;line-height:1;color:var(--ink);letter-spacing:1px}
.brand-tag{font-family:"Gelasio",serif;font-size:15px;color:var(--ink);margin-top:4px}
.nav a{position:absolute;top:60px;font-size:15px;color:var(--ink);text-decoration:none;white-space:nowrap}
.nav .active{color:var(--orange)}
.nav-underline{left:580px;top:87px;width:106px;height:2px;background:var(--orange)}

/* hero */
.hero{left:0;top:135px;width:1200px;height:450px;background:var(--orange);box-shadow:0 10px 14px -8px rgba(0,0,0,.25)}
.hero-photo{left:0;top:0;width:443px;height:450px;background:linear-gradient(160deg,#f4f4f4 0%,#e9e9e9 55%,#c99a7a 80%,#f3b38f 100%)}
.hero-title{right:112px;top:158px;text-align:right;color:var(--white);font-weight:700;font-size:26px;line-height:31px}
.btn-dark{right:113px;top:241px;width:105px;height:32px;background:#111;color:var(--white);font-size:14px;line-height:32px;text-align:center}
.dots{left:1130px;top:413px;display:flex;gap:7px}
.dots span{width:9px;height:9px;border-radius:50%;border:1.5px solid #222}
.dots .on{background:#222}

/* about */
.section-title{font-weight:700;color:var(--ink)}
.about-title{left:0;width:1200px;top:630px;text-align:center;font-size:25px}
.about-text{left:104px;width:992px;top:682px;text-align:center;font-size:11.5px;line-height:22px;color:#333}
.btn-orange{left:539px;top:799px;width:121px;height:33px;background:var(--orange);color:var(--white);font-size:14px;line-height:33px;text-align:center}

/* services */
.services{left:98px;top:912px;width:1002px;height:246px;border:1px solid var(--line);display:flex}
.service{position:relative;flex:1;border-right:1px solid var(--line);text-align:center;padding-top:33px}
.service:last-child{border-right:none}
.service .icon{width:54px;height:54px;margin:0 auto;display:block}
.service h3{font-size:15px;font-weight:700;color:var(--ink);margin-top:21px}
.service p{font-size:11px;line-height:18px;color:#444;margin-top:8px}
.service .more{font-size:12.5px;color:#8a4b1a;margin-top:16px;display:flex;justify-content:center;align-items:center;gap:10px}
.service.active{background:var(--orange)}
.service.active h3,.service.active p{color:var(--white)}
.service.active .more{color:#7a4a16}
.service.active::after{content:"";position:absolute;left:50%;bottom:-11px;margin-left:-11px;border-left:11px solid transparent;border-right:11px solid transparent;border-top:11px solid var(--orange)}

/* testimonials */
.testimonials{left:0;top:1238px;width:1200px;height:359px;background:linear-gradient(180deg,#17141a 0%,#2a2230 45%,#3a2d28 75%,#16141a 100%)}
.test-title{left:0;width:1200px;top:35px;text-align:center;color:var(--white);font-size:25px;font-weight:700}
.avatar{left:548px;top:92px;width:104px;height:104px;border-radius:50%;border:4px solid var(--white);background:linear-gradient(180deg,#6fb0d8,#3d7fa8)}
.quote{left:240px;width:720px;top:220px;text-align:center;color:#e9e9e9;font-style:italic;font-size:12.5px;line-height:21px}
.author{left:0;width:1200px;top:295px;text-align:center;color:var(--white);font-size:12px}
.author b{font-size:13px}
.qmark{color:#bdbdbd;font-family:"Gelasio",serif;font-size:90px;line-height:1}

/* gallery & news */
.block-title{font-size:24px;font-weight:700;color:var(--ink)}
.arrows{display:flex;gap:7px}
.arrows span{width:24px;height:24px;display:flex;align-items:center;justify-content:center}
.arrows .prev{background:var(--orange)}
.arrows .next{background:#1b1b1b}
.gallery-img{top:1715px;width:237px;height:181px}
.news{top:2029px;width:330px;height:130px}
.news-img{left:0;top:0;width:158px;height:130px}
.news-body{left:172px;top:0;width:158px}
.news-body h4{font-size:11.5px;line-height:18px;color:var(--ink);font-weight:700}
.news-meta{font-size:9.5px;color:#666;padding:6px 0 7px;border-bottom:1px solid var(--line)}
.news-body p{font-size:10px;line-height:14px;color:#555;margin-top:7px}
.news-more{font-size:9.5px;color:var(--red);margin-top:8px;display:flex;align-items:center;gap:6px}

/* footer */
.footer{left:0;top:2249px;width:1200px;height:230px;background:var(--footer)}
.footer h5{position:absolute;color:var(--white);font-size:14px;font-weight:400}
.social{top:86px;width:72px;height:93px;text-align:center;color:var(--white);font-size:12px;font-weight:700}
.social i{display:block;width:40px;height:40px;border-radius:50%;background:rgba(0,0,0,.25);margin:14px auto 10px}
.divider{top:43px;width:1px;height:155px;background:#3a3a3a}
.mail-text{left:436px;top:2330px;width:260px;font-size:11px;line-height:20px;color:#9a9a9a}
.mail-input{left:534px;top:2381px;width:199px;height:27px;background:#f2f2f2;font-size:10px;color:#aaa;padding-left:17px;line-height:27px}
.mail-btn{left:733px;top:2381px;width:34px;height:27px;background:var(--orange);display:flex;align-items:center;justify-content:center}
.mail-note{left:534px;top:2416px;font-size:10px;color:#777}
.footer-menu{left:972px;top:2333px;list-style:none}
.footer-menu li{font-size:11.5px;color:var(--white);line-height:21px}
.footer-base{left:0;top:2479px;width:1200px;height:49px;background:var(--footer-base);text-align:center;color:#777;font-size:11px;line-height:49px}
</style>
</head>
<body>

<header>
  <div class="abs brand">
    <div class="brand-name">Halvik.</div>
    <div class="brand-tag">Leadership toolkit for firms on the rise</div>
  </div>
  <nav class="nav">
    <a class="active" style="left:614px">Home</a>
    <a style="left:716px">About Us</a>
    <a style="left:830px">Services</a>
    <a style="left:948px">Gallery</a>
    <a style="left:1045px">Contact Us</a>
  </nav>
  <div class="abs nav-underline"></div>
</header>

<section class="abs hero">
  <div class="abs hero-photo" role="img" aria-label="Photo of a young girl looking up at height marks drawn on a white wall"></div>
  <h1 class="abs hero-title">We are a consultancy firm focused on<br>growth management for Swedish SME's</h1>
  <div class="abs btn-dark">Read More</div>
  <div class="abs dots"><span class="on"></span><span></span><span></span></div>
</section>

<section>
  <h2 class="abs section-title about-title">About Halvik</h2>
  <p class="abs about-text">Lorem ipsum dolor sit amet, consectetur adipiscing elit. Fusce tristique ultricies dui et porta. Sed luctus mauris at dictum auctor. Ut sit amet eleifend tortor, vel fermentum ante. Sed luctus tellus eget tortor mollis, in ullamcorper erat facilisis. Pellentesque bibendum nec nisi ut consectetur. Mauris et elit id est luctus dapibus laoreet scelerisque arcu. Nam varius tincidunt enim quis ultricies. Morbi eleifend, dui faucibus gravida pellentesque, dui lectus tristique ante, et tempor metus ante ut mauris. Quisque feugiat massa ut nisi iaculis pulvinar. Ut euismod mauris enim, ac ultrices massa dignissim ac.</p>
  <div class="abs btn-orange">View More</div>
</section>

<section class="abs services">
  <div class="service">
    <svg class="icon" viewBox="0 0 54 54"><circle cx="27" cy="27" r="26" fill="none" stroke="#222" stroke-width="1.3"/><path d="M18 19v17h18" fill="none" stroke="#222" stroke-width="1.5"/><path d="M22 33v-6M26 33v-9M30 33v-5M34 33v-10" stroke="#222" stroke-width="2"/></svg>
    <h3>Growth Management</h3>
    <p>Praesent turpis mauris, aliquet<br>Gravida adipiscing lectus ut rutrum<br>Aenean at posuere risus.</p>
    <div class="more">Read more <svg width="12" height="8" viewBox="0 0 12 8"><path d="M0 4h10M7 1l3 3-3 3" fill="none" stroke="currentColor" stroke-width="1.3"/></svg></div>
  </div>
  <div class="service">
    <svg class="icon" viewBox="0 0 54 54"><circle cx="27" cy="27" r="26" fill="none" stroke="#222" stroke-width="1.3"/><path d="M27 16a7 7 0 0 0-4 12.7V32h8v-3.3A7 7 0 0 0 27 16z" fill="none" stroke="#222" stroke-width="1.5"/><path d="M24 35h6M25 38h4" stroke="#222" stroke-width="1.5"/></svg>
    <h3>Corporate Communication</h3>
    <p>Praesent turpis mauris, aliquet<br>Gravida adipiscing lectus ut rutrum<br>Aenean at posuere risus.</p>
    <div class="more">Read more <svg width="12" height="8" viewBox="0 0 12 8"><path d="M0 4h10M7 1l3 3-3 3" fill="none" stroke="currentColor" stroke-width="1.3"/></svg></div>
  </div>
  <div class="service active">
    <svg class="icon" viewBox="0 0 54 54"><circle cx="27" cy="27" r="26" fill="none" stroke="#fff" stroke-width="1.3"/><circle cx="27" cy="27" r="21" fill="none" stroke="#fff" stroke-width="1"/><rect x="19" y="20" width="16" height="15" fill="none" stroke="#fff" stroke-width="1.5"/><path d="M19 24h16M23 18v4M31 18v4M22 28h2M26 28h2M30 28h2M22 31h2M26 31h2" stroke="#fff" stroke-width="1.4"/></svg>
    <h3>Project Management</h3>
    <p>Praesent turpis mauris, aliquet<br>Gravida adipiscing lectus ut rutrum<br>Aenean at posuere risus.</p>
    <div class="more">Read more <svg width="12" height="8" viewBox="0 0 12 8"><path d="M0 4h10M7 1l3 3-3 3" fill="none" stroke="currentColor" stroke-width="1.3"/></svg></div>
  </div>
  <div class="service">
    <svg class="icon" viewBox="0 0 54 54"><circle cx="27" cy="27" r="26" fill="none" stroke="#222" stroke-width="1.3"/><path d="M17 26h5v11h-5zM22 27l4-8c2 0 3 1 3 3l-1 4h7c1.5 0 2 1.5 1.5 2.5l-2 7c-.4 1-1 1.5-2 1.5H22" fill="none" stroke="#222" stroke-width="1.5" stroke-linejoin="round"/></svg>
    <h3>Concepetualizing</h3>
    <p>Praesent turpis mauris, aliquet<br>Gravida adipiscing lectus ut rutrum<br>Aenean at posuere risus.</p>
    <div class="more">Read more <svg width="12" height="8" viewBox="0 0 12 8"><path d="M0 4h10M7 1l3 3-3 3" fill="none" stroke="currentColor" stroke-width="1.3"/></svg></div>
  </div>
</section>

<section class="abs testimonials" role="img" aria-label="Night photo of a city skyline with a suspension bridge">
  <h2 class="abs test-title">Testimonials</h2>
  <div class="abs avatar" role="img" aria-label="Portrait photo of the client quoted"></div>
  <svg class="abs" style="left:32px;top:166px" width="22" height="42" viewBox="0 0 22 42"><path d="M20 1L2 21l18 20" fill="none" stroke="#ddd" stroke-width="1.5"/></svg>
  <svg class="abs" style="left:1148px;top:166px" width="22" height="42" viewBox="0 0 22 42"><path d="M2 1l18 20L2 41" fill="none" stroke="#ddd" stroke-width="1.5"/></svg>
  <div class="abs qmark" style="left:204px;top:186px">“</div>
  <div class="abs qmark" style="left:958px;top:276px">”</div>
  <p class="abs quote">Mauris interdum velit leo, ac porta leo vehicula sed. Maecenas iaculis cursus magna. Vestibulum molestie, urna vel lobortis dictum, lacus nibh varius elit, ac tristique sapien dui sit amet diam. Phasellus hendrerit, augue vitae tristique rhoncus, felis urna blandit mauris, vel egestas ex tellus quis leo. Morbi at lacus in</p>
  <div class="abs author"><b>Maren Holt,</b> Lorme ipsum</div>
</section>

<section>
  <h2 class="abs block-title" style="left:94px;top:1651px">Our Gallery</h2>
  <div class="abs arrows" style="left:1046px;top:1655px">
    <span class="prev"><svg width="8" height="10" viewBox="0 0 8 10"><path d="M6 1L2 5l4 4" fill="none" stroke="#fff" stroke-width="1.6"/></svg></span>
    <span class="next"><svg width="8" height="10" viewBox="0 0 8 10"><path d="M2 1l4 4-4 4" fill="none" stroke="#fff" stroke-width="1.6"/></svg></span>
  </div>
  <div class="abs gallery-img" style="left:98px;background:linear-gradient(135deg,#e8e6e3,#8b8c92 60%,#2a2d36)" role="img" aria-label="Photo of business people meeting at a table"></div>
  <div class="abs gallery-img" style="left:354px;background:linear-gradient(180deg,#f1f1f1,#bfbfc2 45%,#2b2c33)" role="img" aria-label="Photo of a business team standing together"></div>
  <div class="abs gallery-img" style="left:608px;background:linear-gradient(135deg,#eef1f4,#9aa3ae 50%,#4a4f58)" role="img" aria-label="Photo of a smiling businessman in an office"></div>
  <div class="abs gallery-img" style="left:864px;background:linear-gradient(135deg,#d8dde4,#9aa4b0 55%,#3a3f48)" role="img" aria-label="Photo of a business handshake in an office"></div>
</section>

<section>
  <h2 class="abs block-title" style="left:98px;top:1950px">Latest News</h2>
  <div class="abs arrows" style="left:1046px;top:1953px">
    <span class="prev"><svg width="8" height="10" viewBox="0 0 8 10"><path d="M6 1L2 5l4 4" fill="none" stroke="#fff" stroke-width="1.6"/></svg></span>
    <span class="next"><svg width="8" height="10" viewBox="0 0 8 10"><path d="M2 1l4 4-4 4" fill="none" stroke="#fff" stroke-width="1.6"/></svg></span>
  </div>

  <article class="abs news" style="left:98px">
    <div class="abs news-img" style="background:linear-gradient(135deg,#e3e3e1,#9b9a98 55%,#3b3a3c)" role="img" aria-label="Photo of colleagues reviewing documents"></div>
    <div class="abs news-body">
      <h4>Lorem ipsum dolor sit amet, consectetur</h4>
      <div class="news-meta">15/05/2016 &nbsp;·&nbsp; Friday</div>
      <p>Mauris interdum velit leo, ac porta leo vehicula sed. Maece-nas iaculis</p>
      <div class="news-more">Read More <svg width="9" height="9" viewBox="0 0 9 9"><circle cx="4.5" cy="4.5" r="3.8" fill="none" stroke="currentColor"/><path d="M3.5 2.8l1.8 1.7-1.8 1.7" fill="none" stroke="currentColor"/></svg></div>
    </div>
  </article>

  <article class="abs news" style="left:435px">
    <div class="abs news-img" style="background:linear-gradient(135deg,#5d86ad,#b9cde0 55%,#2d3e55)" role="img" aria-label="Photo of a business handshake"></div>
    <div class="abs news-body">
      <h4>Lorem ipsum dolor sit amet, consectetur</h4>
      <div class="news-meta">15/05/2016 &nbsp;·&nbsp; Friday</div>
      <p>Mauris interdum velit leo, ac porta leo vehicula sed. Maece-nas iaculis</p>
      <div class="news-more">Read More <svg width="9" height="9" viewBox="0 0 9 9"><circle cx="4.5" cy="4.5" r="3.8" fill="none" stroke="currentColor"/><path d="M3.5 2.8l1.8 1.7-1.8 1.7" fill="none" stroke="currentColor"/></svg></div>
    </div>
  </article>

  <article class="abs news" style="left:772px">
    <div class="abs news-img" style="background:linear-gradient(180deg,#f4efe3,#cdbf9f 50%,#3d3a35)" role="img" aria-label="Photo of people walking in a bright office lobby"></div>
    <div class="abs news-body">
      <h4>Lorem ipsum dolor sit amet, consectetur</h4>
      <div class="news-meta">15/05/2016 &nbsp;·&nbsp; Friday</div>
      <p>Mauris interdum velit leo, ac porta leo vehicula sed. Maece-nas iaculis</p>
      <div class="news-more">Read More <svg width="9" height="9" viewBox="0 0 9 9"><circle cx="4.5" cy="4.5" r="3.8" fill="none" stroke="currentColor"/><path d="M3.5 2.8l1.8 1.7-1.8 1.7" fill="none" stroke="currentColor"/></svg></div>
    </div>
  </article>
</section>

<footer class="abs footer">
  <h5 style="left:98px;top:40px">Let's Connect</h5>
  <div class="abs social" style="left:98px;background:var(--fb)"><i></i>2598</div>
  <div class="abs social" style="left:179px;background:var(--tw)"><i></i>4576</div>
  <div class="abs social" style="left:258px;background:var(--gp)"><i></i>1269</div>
  <div class="abs divider" style="left:436px"></div>
  <h5 style="left:534px;top:40px">Mailing List</h5>
  <div class="abs divider" style="left:875px"></div>
  <h5 style="left:972px;top:40px">Menu</h5>
</footer>
<p class="abs mail-text" style="left:534px">Sign up for our mailing list to get latest updates and offers.</p>
<div class="abs mail-input">Email address</div>
<div class="abs mail-btn"><svg width="12" height="10" viewBox="0 0 12 10"><path d="M1 5l3.5 3.5L11 1.5" fill="none" stroke="#fff" stroke-width="1.8"/></svg></div>
<div class="abs mail-note">We respect your privacy</div>
<ul class="abs footer-menu">
  <li>Home</li><li>About Us</li><li>Services</li><li>Gallery</li><li>Contact Us</li>
</ul>
<div class="abs footer-base">© Copyrights 2015 All Rights Reserved</div>

</body>
</html>
```